IT Company needs Website for new Web and Mobile products for Sports and Fitness

Background:

We developed web based white label frontend web solution, backend services and white label mobile apps for to log, analyze, share and control sport and fitness activities. The name of this product suite is "Trevantix" (http://trevantix-example.com)

This products will be used by customers that provide platforms and community systems for sport and fitness. One of the major USP's is, that our technology i open for nearly all common formats, devices and apps out in the market. This means, you can just upload your data directly from device, file or app - e.G. Kestrel, Bolvane, Ravelo, StrideVault, Pacelumo, Zembra and much others.

Two current concrete examples/References

(1) MyQuorel
It's an international platform from quorel for runners. It provides individual training lans and a training log. MyQuorel uses the Backend Product "Trevantix Hub" (see http://hub.trevantix-example.net for a landing page) to integrate device, file and app support. Before this, every user has to track his training with manual inputs

(2) Paceharbor and fen-zine
Both are German customers. Paceharor is focused on runners. fen-zine is focused on Triatheletes. Both use the Product "Trevantix Web". This is a complete web solution with web based frontend solutions for athletes and coaches.

What do we need?
We need website layout for B2B for our products. We don't need lot's of pages. We need the pretty and nice layout, so we can derive the pages we need.

IMPORTANT
We don't talk about the webpages for the product itself (this will be a different project in future). We talk about a website, explaining the products)
Updates

Hi all,

we just start reviewing the first designs, and try to give feedback as detailed as possible. We attached a PDF document, to describe the the products a little bit more detailed. 

As written in the description, in the end we have two different sections. One is the usual stuff like "start page", "about", "contact", "disclaimer", "pricing", "blah...." and one will be the Developer Section, the "Tec Section". This ist aimed to developers (of our customers) that will integrate our products in there existing system or which will integrate our services in there own software.  This "pages" are more like "documentation", so easy to read and cool to look at (cause developers likes it cool, but straight)

Dear all,

we just do the final review. Cause this week is with heavy load, it takes some time...

Cheers

Odell

Target Market(s)

* Platforms and Communities for sport, health and fitness
* Gyms

Industry/Entity Type

Concrete

Font styles to use
Sans Serif

Requirements
Must have
• * Templates shall base on bootstrap. If not, it shall be easily realized on our site with bootstrap or out of the box "full responsive"

* HTML5 / CSS3
Nice to have
• PAGES
- Start Page
- Generic Template (from which we can derive additional pages)
- Contact Page
- Disclaimer Page
- Blog/News Page
- "About us" Page (can be combined with disclaimer)
- One Example product page (in end we have 3 products), shall show (if you need product details, let me know)
- product and it's description
- pricing information
- Add-Ons for the product
- Developer Section Page (Start Point for developers, where the finde "basic technical concepts and developer API's
- Example Developer Page for technical concept
- Example Developer Page for API

LOGO ISSUE
You can use an align to the Logo attached OR provide a new logo. The given logo is a logo for our own B2C Website http://trevantix-example.net. It's not really necessary, that the logo or the color must be used for the product website. Maybe it will be better if it's a complete new one, to avoid irritation between Trevantix as a B2B product and trevantix-example.net as a B2C platform.
Should not have
• No Flash and other proprietary technologies

```html
<!DOCTYPE html>
<html lang="en">
<head>
<meta charset="utf-8">
<title>Trevantix – Digital Sport and Fitness Services</title>
<link href="https://fonts.googleapis.com/css2?family=PT+Sans:wght@400;700&family=PT+Sans+Narrow:wght@400;700&display=swap" rel="stylesheet">
<style>
:root{
  --orange:#ee7d0f;
  --orange-light:#f7a21a;
  --ink:#3a3a3a;
  --navy:#1f2d3d;
  --muted:#666;
  --line:#dcdcdc;
  --footer:#232323;
  --white:#fff;
}
*{margin:0;padding:0;box-sizing:border-box}
html,body{width:1200px;height:1105px;overflow:hidden;background:var(--white);font-family:"PT Sans",sans-serif;color:var(--ink)}
.page{position:relative;width:1200px;height:1105px}

/* header */
.site-header{position:absolute;left:0;top:0;width:1200px;height:91px;background:var(--white)}
.brand{position:absolute;left:182px;top:14px;display:flex;align-items:center;gap:8px}
.brand-mark{width:22px;height:22px;background:var(--orange)}
.brand-name{font-family:"PT Sans",sans-serif;font-weight:700;font-size:32px;color:var(--orange);line-height:1}
.brand-tagline{position:absolute;left:182px;top:68px;font-size:7.5px;font-weight:700;letter-spacing:.1px;color:#222}
.main-nav{position:absolute;left:410px;top:34px;height:24px;display:flex}
.main-nav a{display:block;height:24px;line-height:24px;font-size:10.5px;color:#555;text-decoration:none;padding:0 30px;border-left:1px solid var(--line)}
.main-nav a:first-child{border-left:none;padding-left:25px}

/* hero */
.hero{position:absolute;left:0;top:91px;width:1200px;height:424px;overflow:hidden}
.hero-photo{position:absolute;inset:0;background:
  radial-gradient(ellipse 380px 300px at 800px 250px,rgba(200,60,40,.55),transparent 70%),
  radial-gradient(ellipse 500px 260px at 180px 80px,#fff6dc,transparent 70%),
  linear-gradient(180deg,#f8d9a6 0%,#f2b66a 45%,#c97a46 80%,#8e5a3c 100%)}
.hero-title{position:absolute;left:182px;top:118px;font-family:"PT Sans Narrow",sans-serif;font-weight:700;font-size:33px;line-height:40px;text-transform:uppercase}
.hero-title .accent{display:block;color:var(--orange)}
.hero-title .dark{display:block;color:#3b3b3b}
.signup{position:absolute;left:180px;top:216px;width:383px;height:39px;background:#f7f7f7;border:1px solid #d7d7d7;border-radius:3px}
.signup-field{position:absolute;left:16px;top:0;line-height:37px;font-size:10px;color:#888}
.signup-button{position:absolute;right:1px;top:1px;width:133px;height:35px;border-radius:3px;background:linear-gradient(#f5b21e,#d88708);color:var(--white);font-size:15.5px;text-align:center;line-height:35px}
.slider-arrow{position:absolute;top:179px;width:42px;height:42px}
.slider-arrow.prev{left:87px}
.slider-arrow.next{left:1081px}
.slider-dot{position:absolute;left:979px;top:403px;width:10px;height:10px;border-radius:50%;background:#e8e4e2}

/* products */
.section-title{position:absolute;left:213px;top:543px;font-family:"PT Sans Narrow",sans-serif;font-weight:700;font-size:23px;color:var(--navy)}
.section-title span{color:var(--orange-light)}
.section-rule{position:absolute;left:214px;top:588px;width:412px;height:6px;background:radial-gradient(ellipse at center,rgba(0,0,0,.07),transparent 70%)}
.product-panel{position:absolute;left:206px;top:626px;width:809px;height:350px;border:1px solid #d6d6d6;border-radius:4px;background:var(--white);box-shadow:inset 0 0 12px rgba(0,0,0,.08)}
.product-tabs{position:absolute;left:33px;top:29px;width:242px}
.product-tab{height:57px;margin-bottom:12px;border:1px solid #d8d8de;border-radius:2px;background:linear-gradient(#fff,#ececf1);padding-left:16px;line-height:55px;font-size:16.5px;color:#2a2a2a;white-space:nowrap}
.product-tab.active{color:var(--orange-light)}
.product-detail{position:absolute;left:307px;top:30px;width:480px}
.detail-heading{font-size:16.5px;color:#555;margin-bottom:4px}
.feature-list{list-style:none;margin:0 0 22px 40px}
.feature-list li{position:relative;padding-left:18px;font-size:11px;line-height:18px;color:#333}
.feature-list li svg{position:absolute;left:0;top:4px}

/* footer */
.site-footer{position:absolute;left:0;top:1021px;width:1200px;height:84px;background:var(--footer);border-top:1px dotted #888}
.social{position:absolute;left:210px;top:22px;display:flex;gap:11px}
.social span{width:22px;height:22px;border-radius:2px}
.copyright{position:absolute;right:229px;top:22px;text-align:right;font-size:11px;line-height:20px;color:#ccc}
</style>
</head>
<body>
<div class="page">

  <header class="site-header">
    <div class="brand"><span class="brand-mark"></span><span class="brand-name">Trevantix</span></div>
    <div class="brand-tagline">DIGITAL SPORT AND FITNESS SERVICES</div>
    <nav class="main-nav">
      <a href="#">HOME</a>
      <a href="#">TREVANTIX</a>
      <a href="#">FITNESS CLOUD</a>
      <a href="#">REFERENCES</a>
      <a href="#">PRODUCTS</a>
      <a href="#">SERVICES</a>
    </nav>
  </header>

  <section class="hero">
    <div class="hero-photo" role="img" aria-label="Close-up of a runner's legs in red running shoes on a road at sunrise"></div>
    <h1 class="hero-title"><span class="accent">Die offene Sport- und</span><span class="dark">Fitnessplatform fur jeden Sport</span></h1>
    <div class="signup">
      <span class="signup-field">WHAT'S YOUR EMAIL ADDRESS :</span>
      <span class="signup-button">JOIN FOR FREE</span>
    </div>
    <svg class="slider-arrow prev" viewBox="0 0 42 42"><circle cx="21" cy="21" r="19.5" fill="none" stroke="#fff" stroke-opacity=".7" stroke-width="2"/><path d="M26 11 L13 21 L26 31 L22 21 Z" fill="#fff" fill-opacity=".7"/></svg>
    <svg class="slider-arrow next" viewBox="0 0 42 42"><circle cx="21" cy="21" r="19.5" fill="none" stroke="#fff" stroke-opacity=".7" stroke-width="2"/><path d="M16 11 L29 21 L16 31 L20 21 Z" fill="#fff" fill-opacity=".7"/></svg>
    <span class="slider-dot"></span>
  </section>

  <h2 class="section-title">Our <span>Products</span></h2>
  <div class="section-rule"></div>

  <section class="product-panel">
    <div class="product-tabs">
      <div class="product-tab active">Trevantix Hub</div>
      <div class="product-tab">Trevantix Web</div>
      <div class="product-tab">Device Communication Agent</div>
      <div class="product-tab">Trevantix Mobile App</div>
    </div>
    <div class="product-detail">
      <h3 class="detail-heading">Backend Data Services</h3>
      <ul class="feature-list">
        <li><svg width="10" height="10" viewBox="0 0 10 10"><circle cx="5" cy="5" r="5" fill="#ee7d0f"/><path d="M4 3 L6.5 5 L4 7Z" fill="#fff"/></svg>Convert data from several formats and provide in one format via normalized</li>
        <li><svg width="10" height="10" viewBox="0 0 10 10"><circle cx="5" cy="5" r="5" fill="#ee7d0f"/><path d="M4 3 L6.5 5 L4 7Z" fill="#fff"/></svg>JSON format</li>
        <li><svg width="10" height="10" viewBox="0 0 10 10"><circle cx="5" cy="5" r="5" fill="#ee7d0f"/><path d="M4 3 L6.5 5 L4 7Z" fill="#fff"/></svg>Pushing data to several platforms</li>
        <li><svg width="10" height="10" viewBox="0 0 10 10"><circle cx="5" cy="5" r="5" fill="#ee7d0f"/><path d="M4 3 L6.5 5 L4 7Z" fill="#fff"/></svg>Retreiving data from file, device, mail or platforms</li>
        <li><svg width="10" height="10" viewBox="0 0 10 10"><circle cx="5" cy="5" r="5" fill="#ee7d0f"/><path d="M4 3 L6.5 5 L4 7Z" fill="#fff"/></svg>Addtional realtime interface (streaming workouts)</li>
        <li><svg width="10" height="10" viewBox="0 0 10 10"><circle cx="5" cy="5" r="5" fill="#ee7d0f"/><path d="M4 3 L6.5 5 L4 7Z" fill="#fff"/></svg>Export data in several common formats (planned for 2014)</li>
      </ul>
      <h3 class="detail-heading">Business Model</h3>
      <ul class="feature-list">
        <li><svg width="10" height="10" viewBox="0 0 10 10"><circle cx="5" cy="5" r="5" fill="#ee7d0f"/><path d="M4 3 L6.5 5 L4 7Z" fill="#fff"/></svg>Data Usage Driven</li>
        <li><svg width="10" height="10" viewBox="0 0 10 10"><circle cx="5" cy="5" r="5" fill="#ee7d0f"/><path d="M4 3 L6.5 5 L4 7Z" fill="#fff"/></svg>Per active user</li>
        <li><svg width="10" height="10" viewBox="0 0 10 10"><circle cx="5" cy="5" r="5" fill="#ee7d0f"/><path d="M4 3 L6.5 5 L4 7Z" fill="#fff"/></svg>Add-Ons as one-time fee</li>
      </ul>
      <h3 class="detail-heading">On-Demand or Dedicated</h3>
    </div>
  </section>

  <footer class="site-footer">
    <div class="social">
      <span style="background:#3b5a9a"></span>
      <span style="background:#3fb5e6"></span>
      <span style="background:#444"></span>
      <span style="background:#f0a030"></span>
      <span style="background:#c9241d"></span>
      <span style="background:#7c95a8"></span>
    </div>
    <div class="copyright">© 2013 trevantix-example.com, All rights reserved<br>X2</div>
  </footer>

</div>
</body>
</html>
```